Gobal construction supply company needs new business card design

I need a business card design for my global supply company using an existing logo. i will be looking to print these on rounded corner cards with the black background version of my logo on the back. on the front white background, my logo again and my simple details.

```html
<!DOCTYPE html>
<html lang="en">
<head>
<meta charset="utf-8">
<title>Meridian Build Supply – Business Card</title>
<link href="https://fonts.googleapis.com/css2?family=Arimo:wght@400;700&family=Montserrat:wght@600&display=swap" rel="stylesheet">
<style>
  :root {
    --stage: #2b2b2b;
    --card-white: #f3f3f3;
    --card-dark: #1e1e1e;
    --ink: #111111;
    --ink-soft: #4a4a4a;
    --accent: #d90000;
    --logo-white: #ffffff;
  }
  * { margin: 0; padding: 0; box-sizing: border-box; }
  html, body {
    width: 1200px; height: 960px; overflow: hidden;
    background: var(--stage);
    font-family: "Arimo", Arial, sans-serif;
  }
  .canvas { position: relative; width: 1200px; height: 960px; }

  .card {
    position: absolute; left: 310px; width: 600px; height: 342px;
    border-radius: 22px; overflow: hidden;
  }
  .card-front { top: 113px; background: var(--card-white); }
  .card-back { top: 511px; background: var(--card-dark); }

  .holder-name {
    position: absolute; left: 39px; top: 40px;
    font-size: 24px; font-weight: 700; color: var(--ink); letter-spacing: 0.3px;
  }
  .holder-role {
    position: absolute; left: 40px; top: 67px;
    font-size: 16px; font-weight: 700; color: var(--accent);
  }
  .address, .contacts {
    position: absolute; font-size: 14px; line-height: 18.5px; color: var(--ink-soft);
  }
  .address { left: 39px; top: 179px; }
  .contacts { left: 42px; top: 226px; }

  .side-band {
    position: absolute; right: 0; top: 0; width: 62px; height: 100%;
    background: var(--card-dark);
  }
  .side-web {
    position: absolute; left: 22px; top: 40px;
    writing-mode: vertical-rl;
    font-size: 14px; font-weight: 700; letter-spacing: 1.6px;
    color: var(--accent);
  }

  .brand {
    position: absolute; left: 0; right: 0; top: 150px;
    display: flex; align-items: center; justify-content: center; gap: 12px;
  }
  .brand-name {
    font-family: "Montserrat", Arial, sans-serif; font-weight: 600;
    font-size: 22px; letter-spacing: 0.5px; color: var(--logo-white);
  }
  .brand-dot { width: 20px; height: 20px; border-radius: 50%; background: var(--accent); }
</style>
</head>
<body>
<div class="canvas">
  <section class="card card-front">
    <h1 class="holder-name">DANIEL REYES</h1>
    <p class="holder-role">CEO/Founder</p>
    <p class="address">2140 Harbor Street<br>Portland, Oregon 97205</p>
    <p class="contacts">
      Ph: 503 214 7780<br>
      Mob: 971 305 6612<br>
      Fax: 503 214 7781<br>
      daniel@meridianbuildsupply.com
    </p>
    <div class="side-band">
      <span class="side-web">www.meridianbuildsupply.com</span>
    </div>
  </section>

  <section class="card card-back">
    <div class="brand">
      <span class="brand-name">MERIDIAN BUILD SUPPLY</span>
      <span class="brand-dot"></span>
    </div>
  </section>
</div>
</body>
</html>
```